Rooted Deep Within: Reshape Your Company with the 6 Laws of Harvest

I'm looking for a design that is clean, like the book "Quiet Harbor" by Lena Voskuil. The book is about the principles of organic farming so I am looking for a color scheme that fits that image.
https://www.shelfmerchant.example/Quiet-Harbor-Calm-Waters-Long-ebook/dp/Z00K493QRT/ref=sr_1_3?crid=58PLQ20ZX44MV&keywords=lena+voskuil&qid=1500000000&s=books&sprefix=lena+%2Cstripbooks%2C250&sr=1-3

I don't want a dark color scheme. I prefer a white or cream book with a bold font.

This book is a good example of what I am looking for:

https://www.shelfmerchant.example/Lantern-Notes-Quiet-Making-Days/dp/0000000000/ref=rtpb_2/000-0000000-0000000?pd_rd_w=ab1c2&pf_rd_p=00000000-0000-0000-0000-000000000000&pf_rd_r=AAAAAAAAAAAAAAAAAAAA&pd_rd_r=00000000-0000-0000-0000-000000000000&pd_rd_wg=x1y2z&pd_rd_i=0000000000&psc=1

Target Market(s)

CEOs and business owners who want to increase the trust in their brands

Industry/Entity Type

Management and Leadership

Colors
00AB8E
00BBA5
67D7C9
C6EFE9
E9F9F6
59FF00
82FF00
B8FF75
E3FFCB
F4FFEA
FFF300
FFF600
FEFA6F
FFFEC7
FFFEE8
FFC000
F8CF3A
FAE287
FDF2CF
FEFAEE

Requirements
Must have
• Author's name is: Martin Keelback
Nice to have
• I have indicated some books that I like. I would be good to have a simple image such as an apple core or the earth's core or some other image of "core" but not absolutely necessary.
Should not have
• I don't want it to have a dark cover or be too heavy

```html
<!DOCTYPE html>
<html lang="en">
<head>
<meta charset="utf-8">
<title>Rooted Deep Within — Book Cover</title>
<link rel="stylesheet" href="https://fonts.googleapis.com/css2?family=Jost:ital,wght@0,400;0,500;0,600;1,400&family=Sacramento&display=swap">
<style>
  :root {
    --page-bg: #f3f3f1;
    --cover-bg: #ffffff;
    --ink: #161616;
    --green-deep: #12c93a;
    --green-bright: #3cff00;
    --fruit-red: #c8261d;
    --fruit-flesh: #f2ecc4;
  }
  * { margin: 0; padding: 0; box-sizing: border-box; }
  html, body {
    width: 1200px;
    height: 794px;
    overflow: hidden;
    background: var(--page-bg);
  }
  .cover {
    position: absolute;
    left: 340px;
    top: 7px;
    width: 520px;
    height: 780px;
    background: var(--cover-bg);
    box-shadow: 0 0 0 1px rgba(0,0,0,0.06);
    font-family: "Jost", "Futura", sans-serif;
    color: var(--ink);
    text-align: center;
  }
  .cover__subtitle {
    position: absolute;
    top: 44px;
    left: 0;
    right: 0;
    font-size: 20px;
    line-height: 24px;
    font-weight: 400;
  }
  .cover__subtitle em { font-style: italic; }
  .cover__title-top {
    position: absolute;
    top: 92px;
    left: 0;
    right: 0;
    font-size: 108px;
    line-height: 1;
    font-weight: 600;
    letter-spacing: -1px;
    background: linear-gradient(90deg, var(--green-deep), var(--green-bright) 55%, var(--green-deep));
    -webkit-background-clip: text;
    background-clip: text;
    color: transparent;
  }
  .cover__title-script {
    position: absolute;
    top: 190px;
    left: 0;
    right: 0;
    font-family: "Sacramento", cursive;
    font-size: 96px;
    line-height: 1;
    color: var(--ink);
    z-index: 2;
  }
  .cover__title-bottom {
    position: absolute;
    top: 268px;
    left: 0;
    right: 0;
    font-size: 122px;
    line-height: 1;
    font-weight: 500;
    letter-spacing: -2px;
    color: var(--ink);
  }
  .cover__artwork {
    position: absolute;
    left: 180px;
    top: 455px;
    width: 176px;
    height: 196px;
    border-radius: 46% 46% 42% 42%;
    background: linear-gradient(180deg, var(--fruit-red) 0%, var(--fruit-red) 22%, var(--fruit-flesh) 30%, var(--fruit-flesh) 76%, var(--fruit-red) 86%, var(--fruit-red) 100%);
  }
  .cover__author {
    position: absolute;
    top: 688px;
    left: 0;
    right: 0;
    font-size: 34px;
    line-height: 1;
    font-weight: 500;
    letter-spacing: 6px;
  }
</style>
</head>
<body>
  <main class="cover">
    <p class="cover__subtitle">Reshape Your Company with the<br><em>6 Laws of Harvest</em></p>
    <h1>
      <span class="cover__title-top">ROOTED</span>
      <span class="cover__title-script">deep</span>
      <span class="cover__title-bottom">WITHIN</span>
    </h1>
    <div class="cover__artwork" role="img" aria-label="Photograph of a bitten red apple core"></div>
    <p class="cover__author">MARTIN KEELBACK</p>
  </main>
</body>
</html>
```